Harbor Crestline (Business Card Design)

Need business cards designed. Something modern, chic, and sleek. Mabye the back of the card should be the navy blue that is in the logo and then just the logo on the back.

Target Market(s)

Those in the hotel, office, and renovation industry

Contact Information for Business Card

1. Logo 2. Dorian Fenwick 3. CEO/Founder 4. Phone: (833) HarbCre / (833) 427-2731 5. Email: dorian@theharborcrestline.com 6. Website: www.theharborcrestline.com

Font styles to use
Other font styles liked:
• Look at the logo font and base the font for everything else off of that.

Colors
0054AA
0677BA
7BADD7
CADEEF
E8F1F8

Requirements
Must have
• Colors that are associated in the logo
Nice to have
• Sleek modern clean and chic design.

```html
<!DOCTYPE html>
<html lang="en">
<head>
<meta charset="utf-8">
<title>Harbor Crestline — Business Card</title>
<link rel="stylesheet" href="https://fonts.googleapis.com/css2?family=Montserrat:wght@300;400;500;700&display=swap">
<style>
  :root {
    --page-bg: #dcdcdc;
    --card-white: #f1f1ef;
    --navy: #272c5a;
    --navy-deep: #1f244d;
    --gold: #d3a73e;
    --ink: #2a2e52;
  }
  * { box-sizing: border-box; margin: 0; padding: 0; }
  html, body { width: 1200px; height: 900px; overflow: hidden; }
  body {
    background: var(--page-bg);
    font-family: "Montserrat", sans-serif;
    display: flex;
    flex-direction: column;
    align-items: center;
    justify-content: center;
    gap: 56px;
  }
  .card {
    width: 630px;
    height: 360px;
    border-radius: 38px;
    position: relative;
    overflow: hidden;
    box-shadow: 0 10px 28px rgba(0, 0, 0, 0.12);
  }
  /* Front side */
  .card--front { background: var(--card-white); color: var(--ink); }
  .front-brand {
    position: absolute;
    top: 46px;
    right: 52px;
    display: flex;
    align-items: center;
    gap: 12px;
    font-weight: 500;
    font-size: 15px;
    letter-spacing: 0.28em;
    text-transform: uppercase;
    color: var(--navy);
  }
  .brand-square {
    width: 14px;
    height: 14px;
    background: var(--gold);
    flex: none;
  }
  .contact {
    position: absolute;
    left: 56px;
    bottom: 46px;
  }
  .contact__name {
    font-weight: 300;
    font-size: 22px;
    letter-spacing: 0.01em;
  }
  .contact__title {
    font-weight: 400;
    font-size: 13px;
    margin-top: 2px;
  }
  .contact__list {
    list-style: none;
    margin-top: 22px;
    display: flex;
    flex-direction: column;
    gap: 10px;
    font-size: 13.5px;
    font-weight: 400;
  }
  .contact__item { display: flex; align-items: center; gap: 12px; }
  .contact__icon { width: 16px; height: 16px; flex: none; }
  .contact__domain { font-weight: 700; }

  /* Back side */
  .card--back {
    background: linear-gradient(135deg, var(--navy) 0%, var(--navy-deep) 100%);
    display: flex;
    align-items: center;
    justify-content: center;
  }
  .back-brand {
    display: flex;
    align-items: center;
    gap: 14px;
    font-weight: 500;
    font-size: 26px;
    letter-spacing: 0.24em;
    text-transform: uppercase;
    color: #ffffff;
  }
</style>
</head>
<body>
  <section class="card card--front" aria-label="Business card front">
    <div class="front-brand">
      <span>Harbor Crestline</span>
      <span class="brand-square"></span>
    </div>
    <div class="contact">
      <p class="contact__name">Dorian Fenwick</p>
      <p class="contact__title">CEO/Founder</p>
      <ul class="contact__list">
        <li class="contact__item">
          <svg class="contact__icon" viewBox="0 0 16 16" aria-hidden="true">
            <rect x="1.5" y="3" width="13" height="10" rx="1" fill="none" stroke="currentColor" stroke-width="1.4"/>
            <path d="M2 4 L8 9 L14 4" fill="none" stroke="currentColor" stroke-width="1.4"/>
          </svg>
          <span>dorian@<span class="contact__domain">theharborcrestline.com</span></span>
        </li>
        <li class="contact__item">
          <svg class="contact__icon" viewBox="0 0 16 16" aria-hidden="true">
            <path d="M4.2 1.8 L6.3 4.6 L5 6.1 C5.8 7.9 7.3 9.6 9.4 10.9 L10.9 9.6 L13.9 11.6 L12.8 14 C7.4 13.6 2.3 8.6 2 3.1 Z" fill="currentColor"/>
          </svg>
          <span>(833) HarbCre / (833) 427-2731</span>
        </li>
      </ul>
    </div>
  </section>

  <section class="card card--back" aria-label="Business card back">
    <div class="back-brand">
      <span>Harbor Crestline</span>
      <span class="brand-square"></span>
    </div>
  </section>
</body>
</html>
```